Marlow Estate Fixers (Handyman / Home Improvement Company)

Looking for a double sided professional looking business card with Logo attached to be highlighted on one side and throwing in an image of a handyman as an option would be nice to see as well. We are a company focused on providing quality Handyman and Home improvement services in a timely manner that is done right the first time with integrity

Industry/Entity Type

Handyman / Home Improvement

Contact Information for Business Card

(LOGO, Name, Mobile and office phone numbers, email) on front side of card, (the words "The SOLUTION to all of your Handyman and Home Improvement needs" followed by "Family Owned and Operated" at the very bottom) on the back.

Colors
EB3D1F
EC4F4E
F09395
F8D3D4
FCEDEE

Requirements
Must have
• Red, Gray, Black Color scheme
Should not have
• No Yellow or Blue colors

```html
<!DOCTYPE html>
<html lang="en">
<head>
<meta charset="utf-8">
<title>Marlow Estate Fixers – Business Card</title>
<link rel="stylesheet" href="https://fonts.googleapis.com/css2?family=Archivo+Black&family=Poppins:wght@400&family=Oswald:wght@500&family=EB+Garamond:ital@1&display=swap">
<style>
  :root {
    --brand-red: #eb2d2f;
    --brand-red-deep: #d82427;
    --ink: #111111;
    --rule-gray: #9a9a9a;
    --paper: #ffffff;
    --backdrop: #2b2b2b;
  }
  * { box-sizing: border-box; margin: 0; padding: 0; }
  html, body { width: 1200px; height: 1108px; overflow: hidden; }
  body {
    background: var(--backdrop);
    display: flex;
    align-items: center;
    justify-content: center;
    gap: 70px;
  }
  .card {
    width: 360px;
    height: 620px;
    border-radius: 22px;
    position: relative;
    overflow: hidden;
  }
  /* Front */
  .card-front {
    background: var(--paper);
    display: flex;
    flex-direction: column;
    align-items: center;
    padding: 120px 28px 52px;
  }
  .brand-name {
    font-family: "Archivo Black", sans-serif;
    font-size: 30px;
    line-height: 1.1;
    color: var(--brand-red);
    text-transform: uppercase;
    text-align: center;
    white-space: nowrap;
  }
  .contact-block {
    margin-top: auto;
    width: 100%;
    display: flex;
    flex-direction: column;
    align-items: center;
  }
  .person-name {
    font-family: "Archivo Black", sans-serif;
    font-size: 24px;
    font-weight: 400;
    color: var(--brand-red);
    letter-spacing: 0.5px;
    text-transform: uppercase;
  }
  .icon-divider {
    width: 100%;
    display: flex;
    align-items: center;
    gap: 10px;
    margin: 14px 0 12px;
  }
  .icon-divider .rule { flex: 1; height: 1px; background: var(--rule-gray); }
  .icon-row { display: flex; gap: 6px; }
  .icon-tile {
    width: 30px; height: 30px;
    border-radius: 5px;
    background: var(--brand-red);
    display: flex; align-items: center; justify-content: center;
  }
  .contact-line {
    font-family: "Poppins", sans-serif;
    font-size: 19px;
    color: var(--ink);
    line-height: 1.4;
  }
  /* Back */
  .card-back {
    background: radial-gradient(circle at 50% 40%, var(--brand-red) 0%, var(--brand-red-deep) 100%);
    display: flex;
    flex-direction: column;
    align-items: center;
    padding: 0 24px 44px;
  }
  .back-mark {
    margin-top: 240px;
    align-self: flex-end;
    margin-right: 20px;
    font-family: "Archivo Black", sans-serif;
    font-size: 13px;
    line-height: 1.1;
    color: var(--paper);
    text-transform: uppercase;
    text-align: center;
  }
  .tagline {
    margin-top: auto;
    text-align: center;
    font-family: "Oswald", sans-serif;
    font-weight: 500;
    color: var(--paper);
    text-transform: uppercase;
    line-height: 1.08;
    white-space: nowrap;
  }
  .tagline .lead { display: block; font-size: 21px; margin-bottom: 4px; }
  .tagline .main { display: block; font-size: 33px; }
  .family-note {
    margin-top: 12px;
    font-family: "EB Garamond", serif;
    font-style: italic;
    font-size: 19px;
    color: var(--paper);
    white-space: nowrap;
  }
</style>
</head>
<body>

  <section class="card card-front" aria-label="Card front">
    <p class="brand-name">Marlow<br>Estate Fixers</p>

    <div class="contact-block">
      <h1 class="person-name">Daniel Reyes</h1>
      <div class="icon-divider">
        <span class="rule"></span>
        <div class="icon-row">
          <span class="icon-tile" aria-label="Mobile">
            <svg width="14" height="18" viewBox="0 0 14 18"><rect x="1.5" y="1" width="11" height="16" rx="2" fill="none" stroke="#fff" stroke-width="1.6"/><circle cx="7" cy="14" r="1" fill="#fff"/></svg>
          </span>
          <span class="icon-tile" aria-label="Office phone">
            <svg width="18" height="16" viewBox="0 0 18 16"><path d="M2 5 Q9 0 16 5 L14 7 L12 5.5 L6 5.5 L4 7 Z" fill="#fff"/><rect x="4" y="8" width="10" height="7" rx="1.5" fill="#fff"/></svg>
          </span>
          <span class="icon-tile" aria-label="Email">
            <svg width="18" height="14" viewBox="0 0 18 14"><rect x="1" y="1" width="16" height="12" fill="none" stroke="#fff" stroke-width="1.5"/><path d="M1 1 L9 8 L17 1" fill="none" stroke="#fff" stroke-width="1.5"/></svg>
          </span>
        </div>
        <span class="rule"></span>
      </div>
      <p class="contact-line">044-555 210 347</p>
      <p class="contact-line">044-555 210 348</p>
      <p class="contact-line">hello@marlowfixers.com</p>
    </div>
  </section>

  <section class="card card-back" aria-label="Card back">
    <span class="back-mark">Marlow<br>Estate Fixers</span>
    <h2 class="tagline">
      <span class="lead">Your solution to all of your</span>
      <span class="main">Handyman and home</span>
      <span class="main">improvement needs</span>
    </h2>
    <p class="family-note">Family Owned and Operated</p>
  </section>

</body>
</html>
```